Dynamic Business Card for Sports Supplements Company

Hi! I'm looking for an awesome business card to match my existing sports supplement company. I have uploaded my current company logo and screenshot of the front page of my website.

I would like to have something dynamic and interesting and utilize the colors in the website - the reds and purples

The business card should be double sided and focus on a unique eye-catching design on the back and include all the relevant company info.

Most importantly, it should say somewhere: "Sign up on our website for a coupon code."

Target Market(s)

Mostly for women gym goers but it shouldn't be too feminine. It should be in keeping with the website design. It should flow and clearly be connected to it

Industry/Entity Type

Business

Contact Information for Business Card

Lorraine K. Vestal
CEO
LVestal@Quorvanexco.com
www.quorvanexco.com
555.417.3820
P.O. Box 47315
Ashcombe, Ohio 00000

Sign up on our website for a coupon code

Font styles to use
Serif
Sans Serif
Other font styles liked:
• Novecento font family and "Quorvanex" is in AR Destine font

Requirements
Must have
• One side should be a bold Quorvanex logo design. Even just the symbol itself may be o.k. (see attached file)

```html
<!DOCTYPE html>
<html lang="en">
<head>
<meta charset="utf-8">
<title>Quorvanex Business Card</title>
<link href="https://fonts.googleapis.com/css2?family=Montserrat:wght@400;500;700;800&display=swap" rel="stylesheet">
<style>
  :root {
    --page: #3a3a3a;
    --card: #050505;
    --ink: #ffffff;
    --accent: #e3262b;
    --rule: #8a8a8a;
  }
  * { margin: 0; padding: 0; box-sizing: border-box; }
  html, body { width: 1200px; height: 855px; overflow: hidden; }
  body {
    background: var(--page);
    font-family: "Montserrat", sans-serif;
    color: var(--ink);
    display: flex;
    flex-direction: column;
    align-items: center;
    justify-content: center;
    gap: 40px;
  }
  .card {
    width: 640px;
    height: 366px;
    background: var(--card);
    position: relative;
    box-shadow: 0 8px 24px rgba(0,0,0,0.45);
  }

  /* Back side */
  .card-back {
    display: flex;
    align-items: center;
    padding-left: 110px;
    padding-bottom: 40px;
  }
  .back-brand {
    display: flex;
    align-items: center;
    gap: 8px;
    margin-right: 22px;
  }
  .brand-square {
    width: 16px;
    height: 16px;
    background: var(--accent);
  }
  .back-brand .brand-name {
    font-size: 17px;
    font-weight: 800;
    letter-spacing: 1px;
    text-transform: uppercase;
  }
  .coupon-line {
    font-size: 13px;
    font-weight: 500;
    letter-spacing: 0.4px;
  }
  .coupon-line .highlight { color: var(--accent); }

  /* Front side */
  .card-front {
    display: flex;
    align-items: center;
  }
  .front-brand {
    width: 330px;
    display: flex;
    flex-direction: column;
    align-items: center;
    padding-top: 60px;
  }
  .front-brand .brand-row {
    display: flex;
    align-items: center;
    gap: 12px;
  }
  .front-brand .brand-square { width: 26px; height: 26px; }
  .front-brand .brand-name {
    font-size: 36px;
    font-weight: 800;
    letter-spacing: 1px;
    text-transform: uppercase;
  }
  .tagline {
    margin-top: 6px;
    font-size: 12px;
    font-weight: 500;
    letter-spacing: 1.6px;
    text-transform: uppercase;
  }
  .divider {
    width: 1px;
    height: 160px;
    background: var(--rule);
  }
  .contact {
    padding-left: 26px;
    font-size: 15px;
    line-height: 1.3;
  }
  .person-name {
    color: var(--accent);
    font-size: 21px;
    font-weight: 700;
    letter-spacing: 0.4px;
  }
  .person-title { font-size: 15px; margin-bottom: 14px; }
  .address { margin-bottom: 14px; }
  .contact-list { list-style: none; }
  .contact-list li { display: flex; align-items: center; gap: 8px; }
  .contact-list svg { width: 13px; height: 13px; flex: none; }
</style>
</head>
<body>

  <section class="card card-back" aria-label="Card back">
    <div class="back-brand">
      <span class="brand-square"></span>
      <span class="brand-name">Quorvanex</span>
    </div>
    <p class="coupon-line">Sign up on our website for a <span class="highlight">coupon code</span></p>
  </section>

  <section class="card card-front" aria-label="Card front">
    <div class="front-brand">
      <div class="brand-row">
        <span class="brand-square"></span>
        <span class="brand-name">Quorvanex</span>
      </div>
      <p class="tagline">Built For Your Best Lift</p>
    </div>
    <div class="divider"></div>
    <div class="contact">
      <p class="person-name">Lorraine K. Vestal</p>
      <p class="person-title">CEO</p>
      <p class="address">P.O. Box 47315<br>Ashcombe, Ohio 00000</p>
      <ul class="contact-list">
        <li>
          <svg viewBox="0 0 24 24" aria-hidden="true"><path fill="#e3262b" d="M6.6 10.8a15 15 0 0 0 6.6 6.6l2.2-2.2a1 1 0 0 1 1-.25 11.4 11.4 0 0 0 3.6.57 1 1 0 0 1 1 1V20a1 1 0 0 1-1 1A17 17 0 0 1 3 4a1 1 0 0 1 1-1h3.5a1 1 0 0 1 1 1c0 1.25.2 2.45.57 3.57a1 1 0 0 1-.25 1z"/></svg>
          <span>555.417.3820</span>
        </li>
        <li>
          <svg viewBox="0 0 24 24" aria-hidden="true"><path fill="#e3262b" d="M2 5h20v14H2z"/><path fill="none" stroke="#050505" stroke-width="2" d="M2 5l10 8 10-8"/></svg>
          <span>LVestal@Quorvanexco.com</span>
        </li>
        <li>
          <svg viewBox="0 0 24 24" aria-hidden="true"><g fill="none" stroke="#e3262b" stroke-width="2"><circle cx="12" cy="12" r="10"/><ellipse cx="12" cy="12" rx="4" ry="10"/><path d="M2 12h20"/></g></svg>
          <span>www.quorvanexco.com</span>
        </li>
      </ul>
    </div>
  </section>

</body>
</html>
```